Larkfield Ridge Management

I need a professional website. My current website is larkfieldridgemanagement.com and I hate it. It was created with some AI tool very quickly because I needed a site up and running with no advanced notice. I’m open to all designs .. I trust you, the professionals will deliver the results I’m anxiously awaiting! :)

```html
<!DOCTYPE html>
<html lang="en">
<head>
<meta charset="utf-8">
<title>Larkfield Ridge Management</title>
<link href="https://fonts.googleapis.com/css2?family=Poppins:wght@300;400;500;600;700&display=swap" rel="stylesheet">
<style>
:root{
  --red:#8c1a2b;
  --red-dark:#6e1422;
  --pink:#c9868e;
  --ink:#1f232d;
  --navy:#203253;
  --slate:#9aa4b6;
  --text:#2a2a2a;
  --muted:#5d6270;
  --line:#d9d9d9;
  --white:#ffffff;
}
*{box-sizing:border-box;margin:0;padding:0}
html,body{width:1200px;height:5133px;overflow:hidden}
body{font-family:"Poppins",sans-serif;color:var(--text);background:var(--white);position:relative}
.abs{position:absolute}
.decor{position:absolute;left:0;top:0;z-index:1}
.layer{z-index:2}
.photo{position:absolute;z-index:2}
.btn{position:absolute;z-index:3;background:var(--red);color:var(--white);font-size:12px;font-weight:600;letter-spacing:.3px;display:flex;align-items:center;justify-content:center;text-transform:uppercase}
.btn.light{background:var(--white);color:var(--ink)}
h2.section-title{position:absolute;z-index:3;left:0;width:1200px;text-align:center;font-size:36px;font-weight:400}
h2.section-title b{font-weight:600}

/* header */
.topbar{position:absolute;z-index:3;top:0;left:0;width:1200px;height:36px}
.topbar .social{position:absolute;left:350px;top:10px;display:flex;gap:22px}
.topbar .contact{position:absolute;right:58px;top:10px;display:flex;gap:34px;color:var(--white);font-size:11.5px}
.topbar .contact span{display:flex;gap:8px;align-items:center}
.brand{position:absolute;z-index:3;left:56px;top:14px;width:112px;display:flex;flex-direction:column;align-items:center;gap:4px}
.brand .mark{width:22px;height:22px;background:var(--red)}
.brand .name{font-size:13px;font-weight:700;color:var(--navy);text-align:center;line-height:1.15}
.nav{position:absolute;z-index:3;top:72px;left:330px;display:flex;gap:0;font-size:13px;color:var(--text)}
.nav a{text-decoration:none;color:inherit;margin-right:58px}
.nav a.active{color:var(--red);font-weight:600}
.nav a:last-child{margin-right:0}

/* hero */
.hero-title{position:absolute;z-index:3;left:158px;top:302px;color:var(--white);font-size:42px;font-weight:600;line-height:1.17}
.hero-sub{position:absolute;z-index:3;left:162px;top:452px;color:var(--white);font-size:13px}

/* about */
.about-copy{position:absolute;z-index:3;left:270px;width:660px;top:862px;color:var(--white);font-size:13px;line-height:1.5;text-align:center}
.about-copy p{margin-bottom:18px}

/* services */
.svc-card{position:absolute;z-index:3;background:var(--white);box-shadow:0 4px 24px rgba(0,0,0,.12);padding:44px 42px 0}
.svc-card h3{font-size:21px;font-weight:500;color:var(--ink);margin-bottom:20px}
.svc-card p{font-size:12.5px;line-height:1.55;color:var(--muted);margin-bottom:18px}
.svc-card a{font-size:12.5px;color:var(--red);text-decoration:underline}

/* projects */
.project{position:absolute;z-index:3;width:280px;text-align:center;color:var(--white)}
.project h4{font-size:14px;font-weight:500;margin-bottom:6px}
.project p{font-size:11px;line-height:1.35}

/* why */
.why{position:absolute;z-index:3;width:200px;text-align:center}
.why .ring{width:142px;height:142px;border-radius:50%;border:2px dashed var(--red);margin:0 auto 18px;display:flex;align-items:center;justify-content:center;background:#fdf6f7}
.why h4{font-size:13.5px;font-weight:600;line-height:1.3}

.clients{position:absolute;z-index:3;top:4112px;left:190px;width:820px;display:flex;justify-content:space-between;align-items:center}
.client{display:flex;align-items:center;gap:8px;font-size:17px;font-weight:600;color:#555}
.client i{display:block;width:14px;height:14px;background:#555}

/* contact */
.form-card{position:absolute;z-index:3;left:362px;top:4292px;width:476px;height:563px;background:var(--white);border-radius:14px 14px 0 0;padding:48px 42px 0}
.form-card .eyebrow{text-align:center;font-size:12px;color:var(--muted)}
.form-card h3{text-align:center;font-size:29px;font-weight:500;margin-bottom:30px}
.field{border-bottom:1px solid var(--line);font-size:11px;color:#777;padding-bottom:12px;height:48px;display:flex;align-items:flex-end}
.row{display:flex;gap:24px;margin-bottom:14px}
.row .field{flex:1}
.captcha{width:228px;height:54px;margin:24px auto 0;border:1px solid var(--line);background:#f9f9f9;display:flex;align-items:center;padding:0 10px;gap:10px;font-size:10px}
.captcha i{display:block;width:18px;height:18px;border:2px solid #bbb;background:var(--white)}

/* footer */
footer{position:absolute;z-index:2;left:0;top:4855px;width:1200px;height:278px;background:var(--ink);color:var(--white)}
.fcol{position:absolute;top:44px;font-size:12px;line-height:1}
.fcol h5{font-size:13px;font-weight:600;margin-bottom:18px}
.fcol li{list-style:none;margin-bottom:17px;font-size:11.5px}
.fcol .ci{display:flex;gap:12px;align-items:center;margin-bottom:14px}
.copy{position:absolute;bottom:14px;width:100%;text-align:center;font-size:11px;color:#cfd2d8}
</style>
</head>
<body>

<!-- decorative bands -->
<svg class="decor" width="1200" height="5133" viewBox="0 0 1200 5133" aria-hidden="true">
  <polygon points="330,0 1200,0 1200,36 298,36" fill="#1f232d"/>
  <rect x="0" y="124" width="1200" height="606" fill="#1f2a3e"/>
  <rect x="0" y="700" width="1200" height="570" fill="#1f232d"/>
  <polygon points="0,1290 950,1160 950,1195 0,1330" fill="#203253"/>
  <polygon points="0,1300 0,1440 330,1268" fill="#9aa4b6"/>
  <polygon points="0,1330 950,1195 1200,1150 1200,1270 0,1440" fill="#ffffff"/>
  <rect x="0" y="2890" width="1200" height="742" fill="#203253"/>
  <polygon points="230,2860 1200,2830 1200,2900 230,2905" fill="#8c1a2b"/>
  <polygon points="800,2905 1200,2820 1200,2990" fill="#c9868e"/>
  <polygon points="0,2888 230,2888 230,2905 0,2905" fill="#203253"/>
</svg>

<!-- header -->
<div class="topbar">
  <div class="social" aria-label="Social links">
    <svg width="14" height="14" viewBox="0 0 14 14"><circle cx="7" cy="7" r="5" fill="none" stroke="#fff" stroke-width="1.4"/></svg>
    <svg width="14" height="14" viewBox="0 0 14 14"><path d="M2 2 12 12 M12 2 2 12" stroke="#fff" stroke-width="1.4"/></svg>
    <svg width="14" height="14" viewBox="0 0 14 14"><rect x="2" y="2" width="10" height="10" rx="3" fill="none" stroke="#fff" stroke-width="1.4"/></svg>
  </div>
  <div class="contact">
    <span><svg width="11" height="11" viewBox="0 0 12 12"><path d="M3 1 5 4 4 5.5C5 7.5 6.5 9 8.5 10L10 9 12 11 10.5 12C5 11 1 7 0 1.5Z" fill="#fff"/></svg>727-555-0143</span>
    <span><svg width="12" height="9" viewBox="0 0 12 9"><rect x=".5" y=".5" width="11" height="8" fill="none" stroke="#fff"/><path d="M.5 .5 6 5 11.5 .5" fill="none" stroke="#fff"/></svg>info@larkfieldridgemanagement.com</span>
  </div>
</div>
<div class="brand"><span class="mark"></span><span class="name">LARKFIELD RIDGE</span></div>
<nav class="nav">
  <a class="active">Home</a><a>About Us</a><a>Services</a><a>How It Works</a><a>News</a><a>Contact Us</a>
</nav>
<div class="btn" style="left:980px;top:63px;width:160px;height:38px;font-size:11px">Book Consultation</div>

<!-- hero -->
<div class="photo" role="img" aria-label="Modern luxury residential tower with curved balconies at dusk" style="left:0;top:124px;width:1200px;height:606px;background:linear-gradient(100deg,#1d2a42 0%,#2b3a55 35%,#6a5a4a 60%,#b58a5e 75%,#3b4660 100%)"></div>
<svg class="decor" style="z-index:2" width="1200" height="760" viewBox="0 0 1200 760" aria-hidden="true">
  <polygon points="122,722 1200,615 1200,700 122,752" fill="#8c1a2b"/>
  <polygon points="700,752 1200,700 1200,752" fill="#6e1422"/>
  <rect x="0" y="752" width="1200" height="8" fill="#1f232d"/>
</svg>
<h1 class="hero-title">Professional Property<br>Management You<br>Can Trust</h1>
<p class="hero-sub">A true partner, not just a vendor.</p>
<div class="btn" style="left:162px;top:490px;width:136px;height:36px;text-transform:none;font-weight:500">Learn More</div>

<!-- about -->
<h2 class="section-title" style="top:790px;color:#fff;font-weight:500">About Us</h2>
<div class="about-copy">
  <p>Lorem Ipsum is simply dummy text of the printing and typesetting industry. Lorem Ipsum has been the industry's standard dummy text ever since the 1500s, when an unknown printer took a galley of type and scrambled it to make a type specimen book.</p>
  <p>Lorem Ipsum is simply dummy text of the printing and typesetting industry. Lorem Ipsum has been the industry's standard dummy specimen book.</p>
  <p>If you're able to become pregnant, you should use effective and reliable birth control while taking a GLP-1 agonist. If you become pregnant while taking the medication, see your healthcare provider immediately.</p>
</div>
<div class="btn" style="left:531px;top:1088px;width:138px;height:38px">Learn More</div>

<!-- services -->
<h2 class="section-title" style="top:1294px"><b>Our</b> Services</h2>

<div class="photo" role="img" aria-label="White residential house with blue metal roof" style="left:600px;top:1398px;width:440px;height:392px;background:linear-gradient(160deg,#5b6f8c,#c9cfd6 45%,#6f7b5e)"></div>
<div class="svc-card" style="left:162px;top:1442px;width:484px;height:304px">
  <h3>Residential Property Management</h3>
  <p>Mobility, productivity, security, costs – which points are particularly important to you and your customers? Avoid friction losses right from the start and talk to an IT partner who understands your business and your concerns. Check us out, we are not afraid of comparison.</p>
  <p>Arrange a free initial consultation today.</p>
  <a>Learn More</a>
</div>

<div class="photo" role="img" aria-label="Modern apartment building with wooden facade panels" style="left:160px;top:1865px;width:440px;height:393px;background:linear-gradient(150deg,#6c88b3,#4a4f5a 50%,#7a5a3d)"></div>
<div class="svc-card" style="left:555px;top:1910px;width:484px;height:304px">
  <h3>Commercial Property Management</h3>
  <p>Contact management, service recording, invoicing, automated correspondence, document management – this and more is what lawyers, trustees and asset managers need in their daily work.</p>
  <p>A specialized software solution can significantly increase your productivity, your billable hours and, above all, the satisfaction of your clients.</p>
  <a>Learn More</a>
</div>

<div class="photo" role="img" aria-label="Tenants reviewing documents with an agent in a living room" style="left:600px;top:2333px;width:440px;height:392px;background:linear-gradient(135deg,#e4dfd6,#b9b2a6 50%,#8a96a8)"></div>
<div class="svc-card" style="left:162px;top:2376px;width:484px;height:304px">
  <h3>Tenant Placement</h3>
  <p>Increased mobility, better availability, lower CapEx, more flexibility – there are many reasons to outsource processes to the cloud.</p>
  <p>A cloud provider must devote enormous resources to security, which is why Norvale Systems maintains a partnership with the two largest and most financially strong providers in the world: Cloudmere and Skyvault.</p>
  <a>Learn More</a>
</div>
<div class="btn" style="left:514px;top:2770px;width:172px;height:36px">View All Services</div>

<!-- projects -->
<h2 class="section-title" style="top:3000px;color:#fff"><b>Our</b> Projects</h2>
<div class="photo" role="img" aria-label="Aerial view of a campus among green trees" style="left:160px;top:3090px;width:278px;height:320px;background:linear-gradient(160deg,#5f7a4a,#a79a7a 50%,#3f5a35)"></div>
<div class="photo" role="img" aria-label="Illuminated high-rise tower at night" style="left:460px;top:3090px;width:278px;height:320px;background:linear-gradient(180deg,#2c3a55,#7a6248 60%,#1e2638)"></div>
<div class="photo" role="img" aria-label="Aerial view of villa estate with gardens" style="left:762px;top:3090px;width:278px;height:320px;background:linear-gradient(160deg,#b8c0b0,#8a8070 45%,#4f6d3c)"></div>
<div class="project" style="left:160px;top:3432px"><h4>Strategy and Planning</h4><p>We have been active in IT for 20 years and are constantly continuing our training across a very broad spectrum.</p></div>
<div class="project" style="left:460px;top:3432px"><h4>Finance and Restructuring</h4><p>We are interested in long-term relation-ships with our customers. We do not pursue short-term strategies.</p></div>
<div class="project" style="left:760px;top:3432px"><h4>Private Investment</h4><p>We understand that IT is a closed book for many of our customers. But that doesn't have to be the case.</p></div>
<div class="btn light" style="left:511px;top:3538px;width:178px;height:38px">View All Projects</div>

<!-- why choose -->
<h2 class="section-title" style="top:3682px"><b>Why Choose</b> US</h2>
<div class="why" style="left:243px;top:3770px">
  <div class="ring"><svg width="64" height="56" viewBox="0 0 64 56" fill="none" stroke="#8c1a2b" stroke-width="2"><circle cx="32" cy="26" r="6"/><circle cx="16" cy="30" r="5"/><circle cx="48" cy="30" r="5"/><path d="M20 50c0-8 24-8 24 0M6 50c0-6 16-6 16 0M42 50c0-6 16-6 16 0"/><path d="M32 4l2 4 4 .5-3 3 .8 4-3.8-2-3.8 2 .8-4-3-3 4-.5z"/></svg></div>
  <h4>10 Year<br>Expertise</h4>
</div>
<div class="why" style="left:496px;top:3770px">
  <div class="ring"><svg width="50" height="60" viewBox="0 0 50 60" fill="none" stroke="#8c1a2b" stroke-width="2"><rect x="4" y="4" width="34" height="46" rx="2"/><path d="M12 16h18M12 24h18M12 32h12"/><circle cx="38" cy="46" r="8"/><path d="M34 46l3 3 5-6"/></svg></div>
  <h4>Residential &amp; Commercial Contracting Experience</h4>
</div>
<div class="why" style="left:748px;top:3770px">
  <div class="ring"><svg width="48" height="56" viewBox="0 0 48 56" fill="none" stroke="#8c1a2b" stroke-width="2.4"><path d="M24 4 42 10v16c0 14-8 22-18 26C14 48 6 40 6 26V10z"/><path d="M15 28l7 7 12-13"/></svg></div>
  <h4>Precision, Safety, And Compliance</h4>
</div>

<!-- clients -->
<h2 class="section-title" style="top:4030px"><b>Our</b> Clients</h2>
<div class="clients">
  <span class="client"><i></i>Halden Springs</span>
  <span class="client">Orvik</span>
  <span class="client">Vantor</span>
  <span class="client"><i></i>Pellmark</span>
  <span class="client">Quillon</span>
</div>

<!-- contact -->
<div class="photo" role="img" aria-label="Modern apartment towers at twilight" style="left:0;top:4200px;width:1200px;height:655px;background:linear-gradient(120deg,#2a3a66 0%,#3f4f7a 40%,#5a5f70 70%,#8a6a4a 100%)"></div>
<div class="form-card">
  <p class="eyebrow">Contact</p>
  <h3>Get In Touch</h3>
  <div class="row"><div class="field">Name*</div><div class="field">Last Name</div></div>
  <div class="row"><div class="field">Phone</div><div class="field">Email Address*</div></div>
  <div class="row"><div class="field">Service</div></div>
  <div class="field" style="height:80px;align-items:flex-start;padding-top:22px">Your Message</div>
  <div class="captcha"><i></i>I'm not a robot</div>
</div>
<div class="btn" style="left:524px;top:4782px;width:152px;height:36px;border-radius:6px">Submit</div>

<!-- footer -->
<footer>
  <div class="abs" style="left:162px;top:78px;width:130px;display:flex;flex-direction:column;align-items:center;gap:8px">
    <span style="width:26px;height:26px;background:var(--red);display:block"></span>
    <span style="font-size:16px;font-weight:700;text-align:center;line-height:1.15">LARKFIELD RIDGE</span>
  </div>
  <div class="fcol" style="left:401px"><h5>Quick Links</h5><ul><li>About</li><li>Services</li><li>Portfolio</li><li>Clients</li><li>Contact Us</li></ul></div>
  <div class="fcol" style="left:547px"><h5>Services</h5><ul><li>Residential Property Management</li><li>Commercial Property Management</li><li>Tenant Placement</li><li>Maintenance Coordination</li></ul></div>
  <div class="fcol" style="left:813px"><h5>Contact Us</h5>
    <div class="ci"><svg width="12" height="12" viewBox="0 0 12 12"><path d="M3 1 5 4 4 5.5C5 7.5 6.5 9 8.5 10L10 9 12 11 10.5 12C5 11 1 7 0 1.5Z" fill="#fff"/></svg>1-888-555-0172</div>
    <div class="ci"><svg width="12" height="9" viewBox="0 0 12 9"><rect x=".5" y=".5" width="11" height="8" fill="none" stroke="#fff"/><path d="M.5 .5 6 5 11.5 .5" fill="none" stroke="#fff"/></svg>info@larkfieldridgemanagement.com</div>
    <div style="width:218px;height:1px;background:#555;margin:4px 0 14px"></div>
    <div style="display:flex;gap:26px">
      <svg width="14" height="14" viewBox="0 0 14 14"><circle cx="7" cy="7" r="5" fill="none" stroke="#fff" stroke-width="1.4"/></svg>
      <svg width="14" height="14" viewBox="0 0 14 14"><path d="M2 2 12 12 M12 2 2 12" stroke="#fff" stroke-width="1.4"/></svg>
      <svg width="14" height="14" viewBox="0 0 14 14"><rect x="2" y="2" width="10" height="10" rx="3" fill="none" stroke="#fff" stroke-width="1.4"/></svg>
    </div>
  </div>
  <p class="copy">Copyright © 2026 brightpathstudio - All Rights Reserved.</p>
</footer>

</body>
</html>
```